Corvanth Veylor - Advanced Skincare and undetectable Makeup for Men

We are in need of a professional webpage for our company Corvanth Veylor. We help every man feel his best by looking his best. Inspired by the myth of Corvanth, we offer makeup and skincare products along with education upon their use. Our mission is to celebrate masculinity in all of its forms, regardless of age, race, sexual orientation, or assigned gender at birth.

The webpage would serve as our online store, as a place where our clients can learn about our brand, view our "How-to" video tutorials, and get product information. An online blog will also be hosted in order to keep clients up to date with news, updates, media mentions, etc.

The color schemes that we use are mostly Black and Gold, with Red accents. please keep in mind that this is a men's cosmetics line, and therefore should read powerful, sexy, confident and bold - all with a high end look and feel.

Think along the lines of brands like Lem Brisko, QDV, Belluti, etc.

our logo is included in the files attached. images and copy will be added in at a later time; hence, general images that fit the feel and filler text is encouraged.

The products to be sold include:
a face cleanser in a pump dispenser bottle (1 size)
a mask in a round jar container (1 size)
a moisturizer in a pump container 1 size)
a concealer in a click pen with a brush applicator (3 shades)
a liquid liner pen (4 shades)
a contouring palette (2 shade options)
a setting spray (single option)

Target Market(s)

Millennial Men

Industry/Entity Type

Beauty

Number of Pages Required

5+ page

Font styles to use
Serif

Colors
ec1f27
000000
faa54b

Requirements
Must have
• ur essential requirements are:
• 1) a stunning and engaging landing page that truly captures the ideals of sexuality, boldness and confidence.
• 2) an interactive and engaging online store that is easy to update / add product / information to.
• 3) Product pages supporting various toggling images of the product, a shade selection option, ingredient information, usage instructions, pricing, and a link to a "how to video" unique to each individual product.
• 4) dedicated space where all of the tutorials can be organized together
• 5) an organized Blog section, that would include a segment for a Q&A section for us to update as the brand grows, ongoing contests (that would be easily hidden if there are no contests running at the moment) as well as general news and updates segment.
• 6) an "about us" page, where our customers are able to learn about our story, inspirations, humanitarian efforts and philosophies in product contents and purity.
• 7) a contact us page, which would include social media links, contact email and telephone number as well as physical address to be updated upon launch.
• 8) discrete privacy policy, terms of use, and return policy links available at the bottom of every page
Nice to have
• 1) A posting forum where clients could post their looks using our products, or maybe a live stream of our Pictoval account.
• 2) a member sign in page so that we can collect and store customer information for faster check out, keep track of purchases attached to their email address (future loyalty program plans) and maintain an email database for email notifications and the such.

```html
<!DOCTYPE html>
<html lang="en">
<head>
<meta charset="utf-8">
<title>Corvanth Veylor</title>
<link href="https://fonts.googleapis.com/css2?family=Cinzel:wght@400;700&family=Roboto:ital,wght@0,400;0,500;0,700;1,400&display=swap" rel="stylesheet">
<style>
:root{
  --gold:#e3a21a;
  --gold-soft:#faa54b;
  --red:#ec1f27;
  --black:#000000;
  --ink:#161616;
  --panel:#1d1d1d;
  --white:#ffffff;
  --grey:#8a8a8a;
  --text-dark:#222222;
}
*{margin:0;padding:0;box-sizing:border-box}
html,body{width:1200px;height:2564px;overflow:hidden;background:var(--ink)}
body{position:relative;font-family:'Roboto',Arial,sans-serif;color:var(--white)}
.abs{position:absolute}
.serif{font-family:'Cinzel','Times New Roman',serif}
svg{display:block}

/* top bar */
.topbar{left:0;top:0;width:1200px;height:39px;background:var(--gold);font-size:13px;font-weight:500}
.topbar .left{left:99px;top:11px}
.topbar .right{right:99px;top:11px;display:flex;gap:10px;align-items:center}
.topbar .sep{opacity:.8;margin:0 8px}
.topbar .item{display:flex;align-items:center;gap:5px}

/* hero */
.hero{left:0;top:39px;width:1200px;height:611px;overflow:hidden}
.hero-photo{left:0;top:0;width:1200px;height:611px;
  background:radial-gradient(circle at 33% 45%,#c98a5e 0%,#6b3a22 18%,#2a1710 36%,transparent 55%),
             radial-gradient(circle at 72% 30%,rgba(227,162,26,.35) 0%,transparent 30%),
             linear-gradient(180deg,#1a120d 0%,#0d0a09 100%)}
.logo{left:99px;top:62px;width:160px;text-align:center}
.logo .mark{width:34px;height:34px;border:2px solid var(--gold);margin:0 auto 10px}
.logo .name{font-family:'Cinzel','Times New Roman',serif;color:var(--gold);font-size:14px;letter-spacing:2px}
.nav{left:518px;top:86px;display:flex;font-size:15px;font-weight:700;letter-spacing:.3px}
.nav a{color:var(--white);text-decoration:none;position:absolute;white-space:nowrap}
.hero-title{left:643px;top:229px;font-size:44px;letter-spacing:4px;font-weight:400}
.hero-text{left:643px;top:296px;width:470px;font-size:17px;line-height:27px}
.btn-outline{left:643px;top:369px;width:167px;height:46px;border:2px solid var(--white);font-size:15px;font-weight:700;display:flex;align-items:center;justify-content:center;gap:6px}

/* about */
.about{left:0;top:543px;width:1200px;height:575px;background:linear-gradient(180deg,#1c1c1c,#141414)}
.about h2{position:absolute;left:99px;top:180px;font-size:36px;font-weight:400;letter-spacing:3px}
.about p{position:absolute;left:99px;top:255px;width:532px;font-size:13.5px;line-height:23.5px;color:#e6e6e6}
.btn-red{background:var(--red);color:var(--white);font-size:14px;font-weight:700;display:flex;align-items:center;justify-content:center;gap:6px}
.about .btn-red{position:absolute;left:99px;top:414px;width:161px;height:44px}
.video{left:687px;top:194px;width:414px;height:264px;background:linear-gradient(135deg,#c7a58f 0%,#8a6a58 45%,#d9c2ae 100%)}
.play{left:183px;top:108px}

/* categories */
.cat{top:1118px;width:400px;height:294px}
.cat-label{position:absolute;font-size:28px;letter-spacing:3px}
.cat-link{position:absolute;font-size:14px;font-weight:700;display:flex;align-items:center;gap:5px}

/* blog */
.blog{left:0;top:1412px;width:1200px;height:639px;background:linear-gradient(180deg,#1a1a1a,#121212)}
.blog h2{position:absolute;left:0;width:1200px;top:104px;text-align:center;font-size:36px;font-weight:400;letter-spacing:4px}
.card{top:200px;width:310px;height:376px;background:var(--white);border:3px solid var(--white)}
.card-img{left:0;top:0;width:304px;height:198px}
.date{left:0;top:135px;width:48px;height:63px;color:var(--white);text-align:center;font-family:'Cinzel','Times New Roman',serif}
.date .d{font-size:22px;font-weight:700;margin-top:6px;line-height:26px}
.date .m{font-size:12px;font-weight:700}
.card h3{position:absolute;left:21px;top:230px;font-size:17px;font-weight:700;color:var(--text-dark)}
.card p{position:absolute;left:21px;top:263px;width:262px;font-size:12.5px;line-height:24px;color:var(--grey);text-align:justify}
.card .rule{position:absolute;left:21px;top:326px;width:262px;height:1px;background:#dcdcdc}
.meta{position:absolute;left:21px;top:343px;width:262px;font-size:11px;color:#555;display:flex;align-items:center;gap:6px}
.meta .more{margin-left:auto;color:var(--red);font-style:italic;font-weight:500;font-size:12px}

/* newsletter */
.news-title{left:0;width:1200px;top:2075px;text-align:center;font-size:20px;letter-spacing:2px}
.news-line{left:0;top:2167px;width:1200px;height:2px;background:var(--red)}
.news-form{left:309px;top:2140px;width:583px;height:56px;border:2px solid var(--red);border-radius:28px;background:#141414;overflow:hidden}
.news-form .ph{position:absolute;left:24px;top:18px;font-size:14px;font-style:italic;color:#dddddd}
.news-form .sub{position:absolute;right:0;top:0;width:169px;height:52px;background:var(--red);border-radius:0 26px 26px 0;font-size:16px;font-weight:700;display:flex;align-items:center;justify-content:center}

/* footer */
.footer{left:0;top:2198px;width:1200px;height:297px;background:#121212}
.fcol{position:absolute;top:70px}
.fcol h4{font-size:16px;font-weight:700;margin-bottom:16px;letter-spacing:.3px}
.fcol li{list-style:none;font-size:13px;line-height:24px;display:flex;align-items:center;gap:18px}
.fcol li::before{content:"»";font-size:13px}
.bottombar{left:0;top:2495px;width:1200px;height:69px;background:var(--gold);text-align:center;font-size:14px;font-weight:500;padding-top:24px}
</style>
</head>
<body>

<header class="abs topbar">
  <div class="abs left">Complimentary Shipping &amp; Returns<span class="sep">|</span>Store Location</div>
  <div class="abs right">
    <span class="item"><svg width="11" height="12" viewBox="0 0 11 12"><rect x="1" y="5" width="9" height="7" fill="#fff"/><path d="M3 5V3.5a2.5 2.5 0 0 1 5 0V5" fill="none" stroke="#fff" stroke-width="1.5"/></svg>Log In</span>
    <span class="sep">|</span>
    <span class="item"><svg width="11" height="12" viewBox="0 0 11 12"><circle cx="5.5" cy="3.5" r="3" fill="#fff"/><path d="M0 12a5.5 5 0 0 1 11 0z" fill="#fff"/></svg>Register</span>
    <span class="sep">|</span>
    <span class="item"><svg width="13" height="12" viewBox="0 0 13 12"><path d="M0 1h2.5l2 7h6.5l1.5-5H4" fill="none" stroke="#fff" stroke-width="1.5"/><circle cx="5.5" cy="10.5" r="1.2" fill="#fff"/><circle cx="10" cy="10.5" r="1.2" fill="#fff"/></svg>My Cart</span>
  </div>
</header>

<section class="abs hero">
  <div class="abs hero-photo" role="img" aria-label="Dark portrait photograph with warm golden light and sparkles"></div>
  <div class="abs logo"><div class="mark"></div><div class="name">Corvanth Veylor</div></div>
  <nav class="abs nav">
    <a style="left:0">HOME</a>
    <a style="left:77px">ABOUT</a>
    <a style="left:160px">PRODUCTS</a>
    <a style="left:270px">HOW TO USE</a>
    <a style="left:396px">BLOG</a>
    <a style="left:468px">CONTACT</a>
    <a style="left:570px;top:1px"><svg width="15" height="15" viewBox="0 0 15 15"><circle cx="6" cy="6" r="4.5" fill="none" stroke="#fff" stroke-width="2"/><path d="M9.5 9.5L14 14" stroke="#fff" stroke-width="2.4"/></svg></a>
  </nav>
  <h1 class="abs hero-title serif">CORVANTH VEYLOR</h1>
  <p class="abs hero-text">At vero eos et accusamus et iusto dignissimos ducimus qui blanditiis praesentium voluptatum deleniti</p>
  <div class="abs btn-outline">READ MORE
    <svg width="15" height="15" viewBox="0 0 15 15"><circle cx="7.5" cy="7.5" r="7" fill="#fff"/><path d="M6 4l3.5 3.5L6 11" fill="none" stroke="#000" stroke-width="2"/></svg></div>
</section>

<section class="abs about">
  <svg class="abs" style="left:0;top:0" width="1200" height="110" viewBox="0 0 1200 110">
    <polygon points="0,0 1200,0 1200,0 600,107 0,0" fill="#0e0a08"/>
    <polygon points="0,0 600,104 1200,0 1200,4 600,112 0,4" fill="var(--gold)"/>
  </svg>
  <h2 class="serif">ABOUT CORVANTH VEYLOR</h2>
  <p>At vero eos et accusamus et iusto odio dignissimos ducimus qui blanditiis praesentium voluptatum deleniti atque corrupti quos dolores et quas molestias excepturi sint occaecati cupiditate non provident, similique sunt in culpa qui officia deserunt mollitia animi, id est laborum et dolorum fuga. Et harum quidem rerum facilis est et expedita distinctio. Nam libero tempore, cum soluta nobis est elig cumque nihuo minus id quod maxime...</p>
  <div class="btn-red">READ MORE
    <svg width="14" height="14" viewBox="0 0 15 15"><circle cx="7.5" cy="7.5" r="7" fill="#fff"/><path d="M6 4l3.5 3.5L6 11" fill="none" stroke="#ec1f27" stroke-width="2"/></svg></div>
  <div class="abs video" role="img" aria-label="Video still of a makeup artist applying product in a studio">
    <svg class="abs play" width="48" height="48" viewBox="0 0 48 48"><circle cx="24" cy="24" r="22" fill="rgba(0,0,0,.55)" stroke="#fff" stroke-width="2"/><path d="M19 14l15 10-15 10z" fill="#fff"/></svg>
  </div>
</section>

<section>
  <div class="abs cat" style="left:0;background:linear-gradient(135deg,#b9aa9c,#6f5f52 60%,#3a3430)" role="img" aria-label="Skin care routine photograph">
    <div class="cat-label serif" style="left:55px;top:193px">SKIN CARE</div>
    <div class="cat-link" style="left:57px;top:243px">VIEW ALL <svg width="13" height="13" viewBox="0 0 15 15"><circle cx="7.5" cy="7.5" r="7" fill="#fff"/><path d="M6 4l3.5 3.5L6 11" fill="none" stroke="#555" stroke-width="2"/></svg></div>
  </div>
  <div class="abs cat" style="left:400px;background:linear-gradient(135deg,#7d6b60,#b59d8c 50%,#5a4d45)" role="img" aria-label="Makeup brush and palette photograph">
    <div class="cat-label serif" style="left:53px;top:44px">MAKEUP</div>
    <div class="cat-link" style="left:54px;top:94px">VIEW ALL <svg width="13" height="13" viewBox="0 0 15 15"><circle cx="7.5" cy="7.5" r="7" fill="#fff"/><path d="M6 4l3.5 3.5L6 11" fill="none" stroke="#555" stroke-width="2"/></svg></div>
  </div>
  <div class="abs cat" style="left:800px;background:linear-gradient(135deg,#4a3f3a,#a88e7e 50%,#c9b3a3)" role="img" aria-label="Eye makeup tutorial photograph">
    <div class="cat-label serif" style="left:60px;top:193px">TUTORIALS</div>
    <div class="cat-link" style="left:61px;top:243px">WATCH NOW <svg width="13" height="13" viewBox="0 0 15 15"><circle cx="7.5" cy="7.5" r="7" fill="#fff"/><path d="M6 4l3.5 3.5L6 11" fill="none" stroke="#555" stroke-width="2"/></svg></div>
  </div>
</section>

<section class="abs blog">
  <h2 class="serif">LATEST BLOG POST</h2>

  <article class="abs card" style="left:99px">
    <div class="abs card-img" style="background:linear-gradient(135deg,#1a1a1a,#6a4a3e 50%,#2a2220)" role="img" aria-label="Close-up photograph of mascara application"></div>
    <div class="abs date" style="background:var(--gold)"><div class="d">11</div><div class="m">JUL</div></div>
    <h3>Shrinking From Toil and Pain</h3>
    <p>Dignissimos et ducimus atque qui blanditiis praesentium voluptatum deleniti et quas.</p>
    <div class="rule"></div>
    <div class="meta"><svg width="10" height="11" viewBox="0 0 11 12"><circle cx="5.5" cy="3.5" r="3" fill="#e3a21a"/><path d="M0 12a5.5 5 0 0 1 11 0z" fill="#e3a21a"/></svg>Ravel Dunmore <span>|</span><svg width="12" height="10" viewBox="0 0 12 10"><path d="M1 1h10v6H5l-3 3V7H1z" fill="#e3a21a"/></svg>0 Comments<span class="more">More »</span></div>
  </article>

  <article class="abs card" style="left:446px">
    <div class="abs card-img" style="background:linear-gradient(135deg,#e8e8e8,#b9a597 50%,#d6d6d6)" role="img" aria-label="Photograph of a person at a makeup table"></div>
    <div class="abs date" style="background:var(--red)"><div class="d">05</div><div class="m">JUL</div></div>
    <h3>Expound The Actual Teachings</h3>
    <p>Dignissimos et ducimus atque qui blanditiis praesentium voluptatum deleniti et quas.</p>
    <div class="rule"></div>
    <div class="meta"><svg width="10" height="11" viewBox="0 0 11 12"><circle cx="5.5" cy="3.5" r="3" fill="#e3a21a"/><path d="M0 12a5.5 5 0 0 1 11 0z" fill="#e3a21a"/></svg>Ravel Dunmore <span>|</span><svg width="12" height="10" viewBox="0 0 12 10"><path d="M1 1h10v6H5l-3 3V7H1z" fill="#e3a21a"/></svg>0 Comments<span class="more">More »</span></div>
  </article>

  <article class="abs card" style="left:791px">
    <div class="abs card-img" style="background:linear-gradient(135deg,#c9a98e,#e9dfcf 55%,#9ba06a)" role="img" aria-label="Photograph of friends wearing face masks"></div>
    <div class="abs date" style="background:var(--gold)"><div class="d">08</div><div class="m">JUL</div></div>
    <h3>Great Explorer Of The Truth</h3>
    <p>Dignissimos et ducimus atque qui blanditiis praesentium voluptatum deleniti et quas.</p>
    <div class="rule"></div>
    <div class="meta"><svg width="10" height="11" viewBox="0 0 11 12"><circle cx="5.5" cy="3.5" r="3" fill="#e3a21a"/><path d="M0 12a5.5 5 0 0 1 11 0z" fill="#e3a21a"/></svg>Ravel Dunmore <span>|</span><svg width="12" height="10" viewBox="0 0 12 10"><path d="M1 1h10v6H5l-3 3V7H1z" fill="#e3a21a"/></svg>0 Comments<span class="more">More »</span></div>
  </article>
</section>

<footer class="abs footer">
  <div class="fcol" style="left:97px"><h4>CUSTOMER CARE</h4><ul><li>Contact Us</li><li>Size Guide</li><li>My Order</li><li>My Account</li><li>Payment</li><li>Authenticity</li></ul></div>
  <div class="fcol" style="left:383px"><h4>SHIPPING &amp; RETURNS</h4><ul><li>Payment</li><li>Save cards</li><li>Shipping</li><li>Return</li><li>Check Out</li></ul></div>
  <div class="fcol" style="left:689px"><h4>COMPANY</h4><ul><li>About Us</li><li>Careers</li><li>Reseller</li><li>Blog Post</li></ul></div>
  <div class="fcol" style="left:902px"><h4>LEGAL AREA</h4><ul><li>Terms and conditions of Sale</li><li>Privacy Policy</li><li>Track your order</li></ul></div>
</footer>

<h2 class="abs news-title serif">SIGN UP TO OUR NEWSLETTER TO STAY UPDATED</h2>
<div class="abs news-line"></div>
<div class="abs news-form"><span class="ph">Your Email Address Here...</span><span class="sub">SUBSCRIBE</span></div>

<div class="abs bottombar">© Copyright 2018 Corvanth Veylor. All Rights Reserved.</div>

</body>
</html>
```